Professional Services - letterhead / business cards

The company (velmora partners) will provide services to Investment Funds and large investors in Spain. I have recently chosen a logo that I am attaching.

I would like a simple stationary design that i could use as letter head, business cards and "with compliments" cards.

I am not quite sure which color I will mostly use for the logo, in the email signature I will probably lean towards the white background and grey letters. I am attaching my favourite options.

Target Market(s)

Large Multinationals, Investment funds and Law firms

Industry/Entity Type

Business

Requirements
Must have
• my details are:
Luis R. Abadal
Velmora Partners S.L.
Casa de Torrelumbre
Calle de Vientoalto 27
28014 Madrid
T: +34 (91) 387-2265
M: +34 (646) 819-054
e-mail: labadal@velmorapartners.com

```html
<!DOCTYPE html>
<html lang="en">
<head>
<meta charset="utf-8">
<title>Velmora Partners – Business Card</title>
<link rel="stylesheet" href="https://fonts.googleapis.com/css2?family=Jost:wght@400;600&display=swap">
<style>
  :root {
    --navy: #25286a;
    --grey: #a9aaae;
    --text-grey: #6d6e72;
    --white: #ffffff;
    --backdrop: #ecebe8;
  }
  * { margin: 0; padding: 0; box-sizing: border-box; }
  html, body { width: 1200px; height: 720px; overflow: hidden; }
  body {
    background: var(--backdrop);
    font-family: "Jost", sans-serif;
    position: relative;
  }
  .card {
    position: absolute;
    top: 210px;
    width: 520px;
    height: 300px;
    border-radius: 22px;
    overflow: hidden;
    box-shadow: 0 6px 18px rgba(0,0,0,0.18);
  }
  .card--front { left: 60px; background: var(--white); }
  .card--back { left: 620px; background: var(--navy); }

  .card__waves { position: absolute; inset: 0; }

  .brand {
    position: absolute;
    left: 0; right: 0;
    text-align: center;
    font-weight: 400;
    letter-spacing: 0.5px;
  }
  .card--front .brand { top: 38px; font-size: 46px; color: var(--navy); }
  .card--back .brand { top: 100px; font-size: 50px; color: var(--white); }

  .address {
    position: absolute;
    top: 118px; left: 0; right: 0;
    text-align: center;
    color: var(--text-grey);
    font-size: 14px;
    line-height: 1.3;
  }

  .holder {
    position: absolute;
    left: 30px; bottom: 34px;
    color: var(--white);
  }
  .holder__name {
    font-weight: 600;
    font-size: 20px;
    letter-spacing: 1px;
    text-transform: uppercase;
  }
  .holder__company { font-size: 13px; }

  .divider {
    position: absolute;
    left: 228px; bottom: 30px;
    width: 1.5px; height: 62px;
    background: var(--white);
  }

  .contacts {
    position: absolute;
    left: 242px; bottom: 28px;
    list-style: none;
    color: var(--white);
    font-size: 14px;
    line-height: 22px;
  }
  .contacts li { display: flex; align-items: center; gap: 8px; }
  .contacts svg { width: 12px; height: 12px; fill: var(--white); flex: none; }

  .website {
    position: absolute;
    bottom: 48px; left: 0; right: 0;
    text-align: center;
    color: var(--white);
    font-size: 14px;
    font-weight: 600;
    letter-spacing: 6px;
  }
</style>
</head>
<body>

  <section class="card card--front">
    <svg class="card__waves" viewBox="0 0 520 300" preserveAspectRatio="none" aria-hidden="true">
      <path fill="var(--grey)" d="M0,168 C160,200 380,182 520,96 L520,104 C380,192 160,214 0,186 Z"/>
      <path fill="var(--navy)" d="M0,194 C160,222 380,200 520,112 L520,300 L0,300 Z"/>
    </svg>

    <div class="brand">velmora partners</div>

    <p class="address">Casa de Torrelumbre, Calle de Vientoalto 27<br>28014 Madrid</p>

    <div class="holder">
      <div class="holder__name">Luis R. Abadal</div>
      <div class="holder__company">Velmora Partners S.L.</div>
    </div>

    <span class="divider"></span>

    <ul class="contacts">
      <li>
        <svg viewBox="0 0 24 24" aria-label="Phone"><path d="M6.6 10.8a15.1 15.1 0 0 0 6.6 6.6l2.2-2.2c.3-.3.7-.4 1-.2 1.1.4 2.3.6 3.6.6.6 0 1 .4 1 1V20c0 .6-.4 1-1 1C10.6 21 3 13.4 3 4c0-.6.4-1 1-1h3.5c.6 0 1 .4 1 1 0 1.3.2 2.5.6 3.6.1.3 0 .7-.2 1z"/></svg>
        +34 (91) 387-2265
      </li>
      <li>
        <svg viewBox="0 0 24 24" aria-label="Mobile"><path d="M7 1h10a2 2 0 0 1 2 2v18a2 2 0 0 1-2 2H7a2 2 0 0 1-2-2V3a2 2 0 0 1 2-2zm0 3v14h10V4zm5 15.5a1.2 1.2 0 1 0 0 2.4 1.2 1.2 0 0 0 0-2.4z"/></svg>
        +34 (646) 819-054
      </li>
      <li>
        <svg viewBox="0 0 24 24" aria-label="Email"><path d="M2 5h20v14H2zm2 2v.5l8 5 8-5V7zm0 2.8V17h16V9.8l-8 5z"/></svg>
        labadal@velmorapartners.com
      </li>
    </ul>
  </section>

  <section class="card card--back">
    <div class="brand">velmora partners</div>
    <div class="website">www.velmorapartners.com</div>
  </section>

</body>
</html>
```